New, modern business card for growing audiology practice

We need a new business card for our audiology practice. Our logo and website have recently changed (more modern) and we want our business cards to reflect this change.
We conduct hearing tests, perform earwax removals, and fit & dispense hearing aids to our patients. We are a family owned practice in which the owner is the one who works directly with the patient. I have attached logos in various formats to use, as well as two ideas I found on this website; as well as a scanned copy of our current logo. Good luck!

Industry/Entity Type

Business

Contact Information for Business Card

Company name: Tolvera Hearing Center
Provider name: Peter Wolstenby, Au.D. F/NSB
Phone number: (440) 683-5127
Address: 837 W. Lindell Ave. Marlow Springs, OH 44187
email: tolverahearing@postvane.com
website: tolverahearing.com

Colors
000000
aaaaaa
dbdbdb
cacaca
9bcb3c
afd23c
cadf82
b1b1b1

Requirements
Must have
• My card must include information in the "details" section. In the attached images, I found a few that I liked and I would like to model after - "brisky bouncin'" and "Sound Method Center".
• Must be horizontal.
• Must include logos provided. I uploaded them in various file formats and various ways.
• Must match logo font, if possible, if not, please get as close as you can.
Nice to have
• I really like the idea of having a color on one side with just the logo and company name and the contact information and provider name on the other side. I also really like the idea of having the main color dominating on the logo/company side with accent of that same color on the contact side of the card.
Should not have
• Must not be vertical.

```html
<!DOCTYPE html>
<html lang="en">
<head>
<meta charset="utf-8">
<title>Tolvera Hearing Center – Business Card</title>
<link rel="stylesheet" href="https://fonts.googleapis.com/css2?family=Roboto:wght@400;500;700&family=Lato:wght@400&display=swap">
<style>
  :root {
    --ink: #000000;
    --paper: #f6f6f6;
    --green: #7aa83a;
    --text-grey: #555555;
    --backdrop: #e4e2de;
    --white: #ffffff;
  }
  html, body {
    margin: 0;
    padding: 0;
    width: 1200px;
    height: 960px;
    overflow: hidden;
    background: var(--backdrop);
  }
  .card {
    position: absolute;
    width: 600px;
    height: 343px;
    box-shadow: 2px 3px 6px rgba(0,0,0,0.35);
    overflow: hidden;
  }
  .card-front {
    left: 314px;
    top: 113px;
    background: var(--paper);
    font-family: "Roboto", Arial, sans-serif;
  }
  .card-back {
    left: 311px;
    top: 472px;
    background: var(--ink);
    font-family: "Lato", Arial, sans-serif;
  }
  .brand-band {
    position: absolute;
    left: 522px;
    top: 29px;
    width: 78px;
    height: 108px;
    background: var(--ink);
  }
  .brand-dot {
    position: absolute;
    left: 462px;
    top: 38px;
    width: 84px;
    height: 84px;
    border-radius: 50%;
    background: var(--green);
  }
  .provider-name {
    position: absolute;
    left: 31px;
    top: 160px;
    margin: 0;
    font-size: 21px;
    font-weight: 700;
    color: var(--green);
    letter-spacing: 0.2px;
  }
  .provider-title {
    position: absolute;
    left: 31px;
    top: 187px;
    margin: 0;
    font-size: 15px;
    font-weight: 500;
    color: var(--ink);
    letter-spacing: 0.3px;
  }
  .address {
    position: absolute;
    left: 31px;
    top: 216px;
    margin: 0;
    font-size: 14px;
    line-height: 18px;
    color: var(--text-grey);
    font-style: normal;
  }
  .contact-list {
    position: absolute;
    left: 31px;
    top: 263px;
    margin: 0;
    padding: 0;
    list-style: none;
    font-size: 14px;
    color: var(--text-grey);
  }
  .contact-list li {
    display: flex;
    align-items: center;
    height: 19.5px;
  }
  .contact-icon {
    width: 13px;
    height: 13px;
    margin-right: 10px;
    fill: var(--green);
  }
  .company-name {
    position: absolute;
    left: 0;
    right: 0;
    top: 155px;
    display: flex;
    justify-content: center;
    align-items: center;
    gap: 12px;
    margin: 0;
    font-size: 28px;
    font-weight: 400;
    color: var(--white);
    letter-spacing: 0.3px;
  }
  .company-dot {
    width: 24px;
    height: 24px;
    border-radius: 50%;
    background: var(--green);
  }
  .website {
    position: absolute;
    left: 0;
    right: 0;
    top: 287px;
    text-align: center;
    margin: 0;
    font-size: 14px;
    letter-spacing: 4px;
    color: var(--white);
  }
  .website .accent { color: var(--green); }
</style>
</head>
<body>

<section class="card card-front" aria-label="Card front">
  <div class="brand-band"></div>
  <div class="brand-dot" aria-label="Tolvera Hearing Center"></div>

  <h1 class="provider-name">PETER WOLSTENBY</h1>
  <p class="provider-title">AU.D. F/NSB</p>

  <address class="address">837 W. Lindell Ave.<br>Marlow Springs, OH 44187</address>

  <ul class="contact-list">
    <li>
      <svg class="contact-icon" viewBox="0 0 24 24" aria-hidden="true"><path d="M6.6 10.8a15.1 15.1 0 0 0 6.6 6.6l2.2-2.2a1 1 0 0 1 1-.25 11.4 11.4 0 0 0 3.6.57 1 1 0 0 1 1 1V20a1 1 0 0 1-1 1A17 17 0 0 1 3 4a1 1 0 0 1 1-1h3.5a1 1 0 0 1 1 1c0 1.25.2 2.45.57 3.57a1 1 0 0 1-.25 1z"/></svg>
      (440) 683-5127
    </li>
    <li>
      <svg class="contact-icon" viewBox="0 0 24 24" aria-hidden="true"><rect x="1" y="5" width="22" height="14"/><path d="M2 6l10 7 10-7" fill="none" stroke="#f6f6f6" stroke-width="2"/></svg>
      tolverahearing@postvane.com
    </li>
    <li>
      <svg class="contact-icon" viewBox="0 0 24 24" aria-hidden="true"><circle cx="12" cy="12" r="10"/><path d="M7 8c2 0 3 1 3 3s-2 2-2 4 2 2 2 4M14 4c0 2 2 3 4 3M15 13c2 0 3 1 3 3" fill="none" stroke="#f6f6f6" stroke-width="1.6"/></svg>
      tolverahearing.com
    </li>
  </ul>
</section>

<section class="card card-back" aria-label="Card back">
  <p class="company-name"><span class="company-dot"></span>TOLVERA HEARING CENTER</p>
  <p class="website">www.<span class="accent">tolverahearing</span>.com</p>
</section>

</body>
</html>
```